Business Management Fortress

Assist with enhancing a powerpoint slide by providing a few design options for consideration. I have a template but open to any creative ideas.

Internal employees and stakeholders

Business Management, Finance, Accounting

• Maintain a fortress, temple, or pyramid schema
• Scenic Background

```html
<!DOCTYPE html>
<html lang="en">
<head>
<meta charset="utf-8">
<title>Business Management Fortress</title>
<link href="https://fonts.googleapis.com/css2?family=Montserrat:wght@500;600&display=swap" rel="stylesheet">
<style>
  :root {
    --stone: #e6e6e6;
    --ink: #111111;
    --white: #ffffff;
    --plum: #9c3866;
    --plum-deep: #8f2f5c;
    --rose: #e04058;
    --rose-deep: #d22e48;
    --tangerine: #f26a3b;
    --tangerine-deep: #e25a2f;
    --amber: #f39a1a;
    --amber-deep: #eb9215;
    --frame-top: #f39a1a;
    --frame-bottom: #9c3866;
  }
  * { margin: 0; padding: 0; box-sizing: border-box; }
  html, body { width: 1200px; height: 675px; overflow: hidden; background: var(--white); }
  body { font-family: "Montserrat", Arial, sans-serif; }
  .slide { position: relative; width: 1200px; height: 675px; background: var(--white); }
  .slide-frame {
    position: absolute; left: 7px; top: 8px; width: 1186px; height: 659px;
    border: 2px solid transparent;
    background: linear-gradient(var(--white), var(--white)) padding-box,
                linear-gradient(180deg, var(--frame-top), var(--frame-bottom)) border-box;
  }
  .roof { position: absolute; left: 0; top: 0; }
  .roof-values {
    position: absolute; top: 102px; left: 0; width: 1200px;
    font-size: 12.5px; font-weight: 500; letter-spacing: 0.3px; color: var(--ink);
  }
  .roof-values span { position: absolute; }
  .band { position: absolute; background: var(--stone); }
  .column-cap, .column-base { position: absolute; height: 9px; }
  .column-shaft, .duty {
    position: absolute; width: 165px; color: var(--white); text-align: center;
  }
  .column-shaft { top: 231px; height: 165px; }
  .column-icon { position: absolute; left: 59px; top: 20px; width: 47px; height: 47px; }
  .column-title {
    position: absolute; left: 0; top: 79px; width: 165px;
    font-size: 17.5px; font-weight: 600; line-height: 32px; letter-spacing: 0.3px;
  }
  .fiduciary-heading {
    position: absolute; top: 403px; left: 0; width: 1200px; text-align: center;
    font-size: 16px; font-weight: 500; letter-spacing: 0.3px; color: var(--ink);
  }
  .duty {
    top: 435px; height: 108px; display: flex; align-items: center; justify-content: center;
    font-size: 14px; font-weight: 600; line-height: 26px; letter-spacing: 0.3px;
  }
  .duty-tight { font-size: 14px; line-height: 26.5px; white-space: nowrap; }
  .is-plum { background: var(--plum); } .is-plum-deep { background: var(--plum-deep); }
  .is-rose { background: var(--rose); } .is-rose-deep { background: var(--rose-deep); }
  .is-tangerine { background: var(--tangerine); } .is-tangerine-deep { background: var(--tangerine-deep); }
  .is-amber { background: var(--amber); } .is-amber-deep { background: var(--amber-deep); }
  .icon-line { fill: none; stroke: var(--white); stroke-width: 1.6; stroke-linecap: round; stroke-linejoin: round; }
</style>
</head>
<body>
<main class="slide">
  <div class="slide-frame"></div>

  <svg class="roof" width="1200" height="140" aria-hidden="true">
    <polygon points="599,58 959,132 241,132" fill="var(--stone)"/>
  </svg>
  <div class="roof-values">
    <span style="left:449px">LEADER</span>
    <span style="left:545px">PARTNER</span>
    <span style="left:649px">PROFITABILITY</span>
  </div>

  <div class="band" style="left:227px; top:144px; width:746px; height:18px"></div>
  <div class="band" style="left:256px; top:172px; width:688px; height:17px"></div>

  <!-- Pillars -->
  <div class="column-cap is-plum-deep" style="left:229px; top:221px; width:179px"></div>
  <div class="column-shaft is-plum" style="left:236px">
    <svg class="column-icon" viewBox="0 0 48 48" aria-hidden="true">
      <g class="icon-line">
        <circle cx="24" cy="17" r="5"/><path d="M13 40c0-7 5-12 11-12s11 5 11 12z"/>
        <circle cx="17" cy="8" r="3"/><circle cx="31" cy="8" r="3"/>
        <circle cx="9" cy="19" r="3.5"/><circle cx="39" cy="19" r="3.5"/>
        <path d="M2 33c0-5 3-8 7-8 2 0 4 1 5 2M46 33c0-5-3-8-7-8-2 0-4 1-5 2"/>
      </g>
    </svg>
    <div class="column-title">PEOPLE</div>
  </div>

  <div class="column-cap is-rose-deep" style="left:417.5px; top:221px; width:179px"></div>
  <div class="column-shaft is-rose" style="left:424.5px">
    <svg class="column-icon" viewBox="0 0 48 48" aria-hidden="true">
      <g class="icon-line">
        <path d="M17 33c0-5-6-8-6-15a13 13 0 0 1 26 0c0 7-6 10-6 15z"/>
        <path d="M18 37h12M19 41h10M21 45h6"/>
        <circle cx="24" cy="19" r="4"/><circle cx="24" cy="19" r="7" stroke-dasharray="3 2.5"/>
        <path d="M24 0v3M9 5l2 2M39 5l-2 2M3 18h3M42 18h3"/>
      </g>
    </svg>
    <div class="column-title">INNOVATION</div>
  </div>

  <div class="column-cap is-tangerine-deep" style="left:605.5px; top:221px; width:179px"></div>
  <div class="column-shaft is-tangerine" style="left:612.5px">
    <svg class="column-icon" viewBox="0 0 48 48" aria-hidden="true">
      <g class="icon-line">
        <rect x="16" y="4" width="16" height="12" rx="1.5"/><path d="M21 4V1h6v3"/>
        <path d="M2 20l8-4 6 16-6 3zM46 20l-8-4-6 16 6 3z"/>
        <path d="M14 19l6-2 8 1 10-2M12 32l8 8c2 2 4 0 3-1l3 3c2 1 4-1 3-2l2 1c2 1 3-1 2-2l-9-9"/>
      </g>
    </svg>
    <div class="column-title">BUSINESS<br>INTELLIGENCE</div>
  </div>

  <div class="column-cap is-amber-deep" style="left:794px; top:221px; width:179px"></div>
  <div class="column-shaft is-amber" style="left:801px">
    <svg class="column-icon" viewBox="0 0 48 48" aria-hidden="true">
      <g class="icon-line">
        <rect x="2" y="4" width="38" height="28" rx="1"/><path d="M18 4V1h6v3M14 32l-4 10M28 32l4 10M0 34h42"/>
        <path d="M9 26v-6M14 26v-9M19 26v-5"/><path d="M8 15l6-4 5 3 7-6"/>
        <circle cx="32" cy="22" r="6"/><path d="M36.5 26.5l8 8"/>
      </g>
    </svg>
    <div class="column-title">STRATEGIC<br>ALLIANCES</div>
  </div>

  <div class="fiduciary-heading">FIDUCIARY RESPONSIBILITIES</div>

  <div class="duty is-plum" style="left:236px">ACCURATE<br>FINANCIALS</div>
  <div class="duty is-rose" style="left:424.5px">INTERNAL<br>CONTROLS</div>
  <div class="duty is-tangerine" style="left:612.5px">BRAND<br>PROTECTION</div>
  <div class="duty duty-tight is-amber" style="left:801px">COMPLIANCE<br>ETHICS<br>COST MANAGEMENT</div>

  <div class="column-base is-plum-deep" style="left:229px; top:542.5px; width:179px"></div>
  <div class="column-base is-rose-deep" style="left:417.5px; top:542.5px; width:179px"></div>
  <div class="column-base is-tangerine-deep" style="left:605.5px; top:542.5px; width:179px"></div>
  <div class="column-base is-amber-deep" style="left:794px; top:542.5px; width:179px"></div>

  <div class="band" style="left:256px; top:584px; width:688px; height:17px"></div>
  <div class="band" style="left:227px; top:612px; width:746px; height:18px"></div>
</main>
</body>
</html>
```